Advanced Therapeutic Massage Therapist

I need a business card advertising my massage services as an advanced therapeutic massage therapist. I offer advanced therapeutic massage, swedish and deep tissue. I want to create a simple, professional and feminine card. I like bright colours and creativity.

I prefer a bold and experimental approach rather than something status-quo. A card to suggest therapeutic healing through dynamic massage. Motifs, shapes or layout which suggest movement and flow.
Updates

Target Market(s)

Everybody!

Industry/Entity Type

Health And Wellness

Contact Information for Business Card

The card should include:
My name, logo, services offered and my contact details.

Sláine Dunleavy
Massage Therapist

- Swedish - Deep Tissue - Advanced Therapeutic

Phone: (+353) 87 216 4093
Email: regenerate@slainedunleavy-example.com
Website: www.slainedunlevy-example.com

Font styles to use
Serif
Sans Serif
Decorative
Script

Colors

Designer to choose colors to be used in the design.

Requirements
Must have
• An example may contain something like this, yet concise:
• "Sláine Dunleavy
• Massage Therapist
• - Swedish - Deep Tissue - Advanced Therapeutic"
Nice to have
• This sentence is optional:
• Imagery such as a logo or symbol. I have attached a file containing a logo I had produced however the name is incorrect now as it is "Sláine" not "Nelly". It could be edited to change it to Sláine.
• I have sent the file as .psd .jpg. .pdf and .png
• I like when the card conveys energy, movement, pressure points, flow etc.
• I just like the designer to follow their own style and ideas. I like bright colours but must have a lot of a base colour to offset it. I really prefer them to follow their own inspiration. That is my preference.
Should not have
• Pine trees, non-native trees to Britain and Ireland, exotic flowers or animals that are not native to Britain and Ireland.
• I don't like brown as the background colour of the card.
• The cars shouldn't look like a wedding invitation i.e too many floral type designs.

```html
<!DOCTYPE html>
<html lang="en">
<head>
<meta charset="utf-8">
<title>Sláine Dunleavy – Massage Therapist Business Card</title>
<link rel="stylesheet" href="https://fonts.googleapis.com/css2?family=Open+Sans:wght@400;600;700&display=swap">
<style>
  :root {
    --backdrop: #3a3431;
    --card: #0e0e0f;
    --card-edge: #1b1b1d;
    --gold: #c9a05a;
    --gold-deep: #8a6428;
    --mint: #bfe3d9;
    --mint-deep: #8cc3b6;
    --ink-light: #f1f1ee;
    --bullet: #c9dcc4;
  }
  * { box-sizing: border-box; margin: 0; padding: 0; }
  html, body { width: 1200px; height: 844px; overflow: hidden; }
  body {
    background: var(--backdrop);
    font-family: "Open Sans", Arial, sans-serif;
    position: relative;
  }
  .card {
    position: absolute;
    top: 267px;
    width: 540px;
    height: 310px;
    background: linear-gradient(160deg, var(--card-edge), var(--card) 60%);
    box-shadow: 0 10px 30px rgba(0,0,0,.45);
  }
  .card--front { left: 40px; }
  .card--back { left: 620px; }

  .emblem {
    position: absolute;
    border-radius: 50%;
    padding: 5px;
    background: radial-gradient(circle, var(--gold) 60%, var(--gold-deep) 100%);
  }
  .emblem__art {
    width: 100%;
    height: 100%;
    border-radius: 50%;
    background: radial-gradient(circle at 45% 40%, #dff3ec 0%, var(--mint) 45%, var(--mint-deep) 100%);
    box-shadow: inset 0 0 0 2px var(--gold-deep);
  }
  .card--front .emblem { left: 38px; top: 44px; width: 150px; height: 150px; }
  .card--back .emblem { left: 185px; top: 70px; width: 170px; height: 170px; }

  .services {
    position: absolute;
    left: 40px;
    bottom: 26px;
    list-style: none;
  }
  .services__item {
    color: var(--ink-light);
    font-weight: 600;
    font-size: 15px;
    line-height: 22px;
    display: flex;
    align-items: center;
    gap: 8px;
  }
  .services__item::before {
    content: "";
    width: 10px;
    height: 10px;
    border-radius: 50%;
    background: var(--bullet);
  }

  .identity {
    position: absolute;
    right: 30px;
    top: 88px;
    text-align: right;
    color: var(--ink-light);
  }
  .identity__name {
    color: var(--gold);
    font-weight: 600;
    font-size: 20px;
    line-height: 24px;
  }
  .identity__title {
    font-size: 13px;
    line-height: 18px;
    margin-bottom: 20px;
  }
  .contact {
    font-size: 13px;
    line-height: 22px;
  }
  .contact__line {
    display: flex;
    justify-content: flex-end;
    align-items: center;
    gap: 8px;
  }
  .contact__icon { width: 12px; height: 12px; fill: var(--gold); }
</style>
</head>
<body>
  <section class="card card--front" aria-label="Business card front">
    <div class="emblem">
      <div class="emblem__art" role="img" aria-label="Ornamental tree of life emblem in gold on soft mint"></div>
    </div>

    <div class="identity">
      <h1 class="identity__name">Sláine Dunleavy</h1>
      <p class="identity__title">Massage Therapist</p>
      <div class="contact">
        <p class="contact__line">(+353) 87 216 4093
          <svg class="contact__icon" viewBox="0 0 24 24" aria-hidden="true"><path d="M6.6 10.8a15.1 15.1 0 0 0 6.6 6.6l2.2-2.2c.3-.3.7-.4 1-.2 1.1.4 2.3.6 3.6.6.6 0 1 .4 1 1V20c0 .6-.4 1-1 1A17 17 0 0 1 3 4c0-.6.4-1 1-1h3.5c.6 0 1 .4 1 1 0 1.3.2 2.5.6 3.6.1.3 0 .7-.2 1z"/></svg>
        </p>
        <p class="contact__line">slainemassage@example.com
          <svg class="contact__icon" viewBox="0 0 24 24" aria-hidden="true"><path d="M2 5h20v14H2z M3.5 6.5 12 13l8.5-6.5" fill="none" stroke="#c9a05a" stroke-width="2"/></svg>
        </p>
      </div>
    </div>

    <ul class="services">
      <li class="services__item">Swedish</li>
      <li class="services__item">Deep Tissue</li>
      <li class="services__item">Advanced Therapeutic</li>
    </ul>
  </section>

  <section class="card card--back" aria-label="Business card back">
    <div class="emblem">
      <div class="emblem__art" role="img" aria-label="Ornamental tree of life emblem in gold on soft mint"></div>
    </div>
  </section>
</body>
</html>
```